Brimlow Plumbing Solutions

This is for my new plumbing company, I have attached an example of what I’m going for but want it to look better.

Target Market(s)

Home owners, real estate, etc.

Industry/Entity Type

Plumbing

Font styles to use
Other font styles liked:
• As per my logo and other examples uploaded

Colors

Designer to choose colors to be used in the design.

Requirements
Must have
• Must include my logo provided and similar to my flyer I have attached but better

```html
<!DOCTYPE html>
<html lang="en">
<head>
<meta charset="utf-8">
<title>Brimlow Plumbing Solutions – Flyer</title>
<link rel="stylesheet" href="https://fonts.googleapis.com/css2?family=Poppins:wght@400;500;600;700&display=swap">
<style>
  :root {
    --backdrop: #93b9d8;
    --paper: #ffffff;
    --navy: #1b3a5c;
    --sky: #8fb6d8;
    --sky-mid: #6d9dc8;
    --orange: #ef7b22;
    --ink: #141a22;
    --white: #ffffff;
  }
  * { box-sizing: border-box; margin: 0; padding: 0; }
  html, body { width: 1200px; height: 1200px; overflow: hidden; }
  body {
    background: var(--backdrop);
    font-family: "Poppins", sans-serif;
    color: var(--ink);
    position: relative;
  }
  .flyer {
    position: absolute;
    left: 234px; top: 61px;
    width: 732px; height: 1078px;
    background: var(--paper);
  }
  .brand {
    position: absolute;
    top: 28px; left: 0; width: 100%;
    display: flex; justify-content: center; align-items: center; gap: 12px;
  }
  .brand-mark { width: 44px; height: 44px; border-radius: 50%; background: var(--navy); flex: none; }
  .brand-text { display: flex; flex-direction: column; line-height: 1.15; }
  .brand-name { font-size: 30px; font-weight: 700; color: var(--ink); letter-spacing: 0.5px; }
  .brand-sub { font-size: 16px; font-weight: 500; color: var(--ink); }
  .brand-tagline { font-size: 13px; font-weight: 400; color: var(--ink); }

  .hero {
    position: absolute;
    left: 0; top: 150px; width: 100%; height: 287px;
    background: var(--navy);
    overflow: hidden;
  }
  .hero-waves { position: absolute; inset: 0; width: 100%; height: 100%; }
  .hero-copy { position: absolute; left: 53px; top: 32px; color: var(--white); }
  .hero-title { font-size: 38px; font-weight: 600; line-height: 1.2; }
  .hero-subtitle { margin-top: 20px; font-size: 28px; font-weight: 400; line-height: 1.3; }
  .hero-subtitle strong { font-weight: 500; }
  .discount-badge {
    position: absolute; left: 548px; top: 120px;
    width: 112px; height: 112px; border-radius: 50%;
    background: var(--orange); color: var(--white);
    display: flex; flex-direction: column; justify-content: center; align-items: center;
    font-size: 16px; font-weight: 500; line-height: 1.3; text-align: center;
  }
  .discount-badge .discount-value { font-size: 20px; font-weight: 600; }

  .section-title { position: absolute; left: 48px; font-size: 27px; font-weight: 500; color: var(--ink); }
  .services-title { top: 474px; }
  .services {
    position: absolute; left: 47px; top: 543px;
    width: 637px;
    display: grid; grid-template-columns: repeat(3, 1fr);
    grid-template-rows: 173px 174px; gap: 11px;
  }
  .service {
    display: flex; flex-direction: column; align-items: center; justify-content: center;
    color: var(--white); font-size: 19px; font-weight: 500; text-align: center; line-height: 1.25;
    gap: 16px;
  }
  .service--light { background: var(--sky); }
  .service--dark { background: var(--navy); }
  .service svg { width: 48px; height: 48px; fill: none; stroke: var(--white); stroke-width: 2; stroke-linecap: round; stroke-linejoin: round; }

  .contact-title { top: 946px; font-size: 25px; }
  .contact-row {
    position: absolute; left: 48px; top: 998px; width: 636px;
    display: flex; align-items: center; gap: 20px; font-size: 14px; color: var(--ink);
  }
  .contact-item { display: flex; align-items: center; gap: 9px; line-height: 1.3; white-space: nowrap; }
  .contact-item svg { width: 22px; height: 22px; fill: var(--ink); flex: none; }
  .social-dots { display: flex; gap: 4px; }
  .social-dots span { width: 18px; height: 18px; border-radius: 50%; background: var(--ink); display: block; }
  .cta {
    margin-left: auto;
    background: var(--orange); color: var(--white);
    font-size: 14px; font-weight: 500;
    padding: 6px 22px; border-radius: 3px; white-space: nowrap;
  }
</style>
</head>
<body>
  <main class="flyer">
    <header class="brand">
      <span class="brand-mark"></span>
      <div class="brand-text">
        <span class="brand-name">BRIMLOW</span>
        <span class="brand-sub">Plumbing Solutions</span>
        <span class="brand-tagline">Reliable Plumbing. Real Solutions</span>
      </div>
    </header>

    <section class="hero">
      <svg class="hero-waves" viewBox="0 0 732 287" preserveAspectRatio="none" aria-hidden="true">
        <path d="M420 0 C480 0 500 40 560 45 C620 50 680 30 732 20 L732 0 Z" fill="#8fb6d8"/>
        <path d="M470 95 C560 70 620 85 732 75 L732 140 C650 150 600 125 520 120 Z" fill="#6d9dc8"/>
        <path d="M0 220 C120 200 200 250 320 245 C420 240 480 200 560 215 C620 225 680 240 732 230 L732 287 L0 287 Z" fill="#6d9dc8"/>
      </svg>
      <div class="hero-copy">
        <h1 class="hero-title">Your Local Reliable<br>Sydney Plumber</h1>
        <p class="hero-subtitle">Specialising in <strong>Plumbing,</strong><br><strong>Drainage &amp; Gas Maintenance</strong></p>
      </div>
      <div class="discount-badge"><span>DISCOUNT</span><span class="discount-value">10% OFF</span></div>
    </section>

    <h2 class="section-title services-title">Key Services</h2>
    <div class="services">
      <div class="service service--light">
        <svg viewBox="0 0 48 48"><path d="M10 10 L30 30 M14 6 L6 14 M28 34 L36 42 L42 36 L34 28 Z"/><circle cx="34" cy="12" r="6"/><path d="M30 16 L18 28"/></svg>
        <span>Blocked Drains</span>
      </div>
      <div class="service service--light">
        <svg viewBox="0 0 48 48"><path d="M14 8 H28 V18 H36 V26 H28"/><path d="M20 26 C17 31 17 34 20 36 C23 34 23 31 20 26 Z"/><circle cx="32" cy="36" r="5"/></svg>
        <span>Leak Detection</span>
      </div>
      <div class="service service--light">
        <svg viewBox="0 0 48 48"><path d="M10 8 H22 V40 H10 Z M22 16 H36 V22 M30 28 H40 V40 H30 Z"/></svg>
        <span>Tap Repairs</span>
      </div>
      <div class="service service--dark">
        <svg viewBox="0 0 48 48"><path d="M8 10 H24 L28 16 H40 V32 H8 Z M14 22 H34 M14 27 H30"/><circle cx="14" cy="38" r="3"/><circle cx="34" cy="38" r="3"/></svg>
        <span>Emergency<br>Plumbing</span>
      </div>
      <div class="service service--dark">
        <svg viewBox="0 0 48 48"><circle cx="14" cy="34" r="6"/><circle cx="34" cy="14" r="6"/><path d="M10 10 L38 38 M38 10 L10 38"/></svg>
        <span>Gas<br>Fitting</span>
      </div>
      <div class="service service--dark">
        <svg viewBox="0 0 48 48"><rect x="8" y="10" width="32" height="26" rx="8"/><path d="M16 24 C20 18 28 18 32 24 M16 28 H32"/></svg>
        <span>Hot Water<br>Systems</span>
      </div>
    </div>

    <h2 class="section-title contact-title">Contact Us</h2>
    <div class="contact-row">
      <div class="contact-item">
        <svg viewBox="0 0 24 24"><path d="M6.6 10.8a15 15 0 0 0 6.6 6.6l2.2-2.2a1 1 0 0 1 1-.25 11.4 11.4 0 0 0 3.6.57 1 1 0 0 1 1 1V20a1 1 0 0 1-1 1A17 17 0 0 1 3 4a1 1 0 0 1 1-1h3.5a1 1 0 0 1 1 1c0 1.25.2 2.45.57 3.6a1 1 0 0 1-.25 1Z"/></svg>
        <span>Call 24/7<br>0400 123 456</span>
      </div>
      <div class="contact-item">
        <svg viewBox="0 0 24 24"><path d="M2 5h20v14H2Z M3.5 6.5 12 13l8.5-6.5" fill="none" stroke="#141a22" stroke-width="2" stroke-linejoin="round"/></svg>
        <span>hello@brimlow.com.au</span>
      </div>
      <div class="contact-item">
        <div class="social-dots"><span></span><span></span><span></span></div>
        <span>@brimlow</span>
      </div>
      <span class="cta">Book Now</span>
    </div>
  </main>
</body>
</html>
```